Harbor Ledger Funds Bus card and Logo

I need a logo design and Bus card design. The fund focuses on evaluating and investing in minerals (sub-surface rights) and real estate.

Harbor ledger refers to a book of knowledge that each plebe gets when entering the Kelmont Marine Academy (my alma mater)

Target Market(s)

Investors and financial advisors

Contact Information for Business Card

Simple - perhaps a logo with a theme on book of knowledge

Logo Text

Ex Scientia Imperium

Font styles to use
Serif
Sans Serif

Colors

Designer to choose colors to be used in the design.

Requirements
Must have
• memorable logo that is relatively simple

```html
<!DOCTYPE html>
<html lang="en">
<head>
<meta charset="utf-8">
<title>Harbor Ledger Funds – Business Card</title>
<link rel="stylesheet" href="https://fonts.googleapis.com/css2?family=Roboto:wght@400&display=swap">
<style>
  :root {
    --paper: #ffffff;
    --ink: #000000;
    --charcoal: #353535;
    --mist: #efefef;
    --light-text: #ffffff;
  }
  * { margin: 0; padding: 0; box-sizing: border-box; }
  html, body { width: 1200px; height: 564px; overflow: hidden; background: var(--paper); }
  .card {
    position: relative;
    width: 1200px;
    height: 564px;
    background: var(--paper);
    font-family: "Roboto", Arial, sans-serif;
    overflow: hidden;
  }
  .front {
    position: absolute;
    left: 0; top: 0;
    width: 600px; height: 564px;
  }
  .brand-mark {
    position: absolute;
    left: 270px; top: 88px;
    width: 60px; height: 60px;
    border: 2px solid var(--ink);
  }
  .brand-name {
    position: absolute;
    left: 0; top: 226px;
    width: 600px;
    text-align: center;
    font-size: 46px;
    font-weight: 400;
    color: var(--ink);
    letter-spacing: 0.5px;
    white-space: nowrap;
  }
  .skyline {
    position: absolute;
    left: 0; top: 355px;
    width: 600px; height: 209px;
    background: linear-gradient(to bottom,
      var(--mist) 0%, var(--mist) 38%,
      var(--charcoal) 42%, var(--charcoal) 100%);
  }
  .back {
    position: absolute;
    left: 600px; top: 0;
    width: 600px; height: 564px;
    background: var(--charcoal);
    color: var(--light-text);
  }
  .back-title {
    position: absolute;
    left: 35px; top: 42px;
    font-size: 45px;
    font-weight: 400;
    white-space: nowrap;
  }
  .contact-row {
    position: absolute;
    left: 31px;
  }
  .contact-icon {
    display: block;
    width: 34px; height: 34px;
  }
  .icon-solid { fill: var(--light-text); }
  .icon-line { fill: none; stroke: var(--light-text); stroke-width: 2.4; }
  .contact-text {
    position: absolute;
    left: 69px;
    font-size: 22px;
    line-height: 26px;
    white-space: nowrap;
  }
  .row-phone { top: 174px; }
  .row-phone .contact-text { top: 4px; }
  .row-web { top: 298px; }
  .row-web .contact-text { top: 4px; }
  .row-address { top: 446px; }
  .row-address .contact-icon { height: 50px; }
  .row-address .contact-text { top: -8px; }
</style>
</head>
<body>
<div class="card">
  <section class="front">
    <div class="brand-mark"></div>
    <h1 class="brand-name">HARBOR LEDGER FUNDS</h1>
    <div class="skyline" role="img" aria-label="City skyline silhouette in dark and light grey"></div>
  </section>

  <section class="back">
    <h2 class="back-title">HARBOR LEDGER FUNDS</h2>

    <div class="contact-row row-phone">
      <svg class="contact-icon icon-solid" viewBox="0 0 24 24" aria-hidden="true">
        <path d="M6.6 10.8c1.4 2.8 3.8 5.1 6.6 6.6l2.2-2.2c.3-.3.7-.4 1-.2 1.1.4 2.3.6 3.6.6.6 0 1 .4 1 1V20c0 .6-.4 1-1 1C10.6 21 3 13.4 3 4c0-.6.4-1 1-1h3.5c.6 0 1 .4 1 1 0 1.3.2 2.5.6 3.6.1.3 0 .7-.2 1z"/>
      </svg>
      <span class="contact-text">HARBOR LEDGER FUNDS</span>
    </div>

    <div class="contact-row row-web">
      <svg class="contact-icon icon-line" viewBox="0 0 34 34" aria-hidden="true">
        <circle cx="17" cy="17" r="15"/>
        <ellipse cx="17" cy="17" rx="6.5" ry="15"/>
        <line x1="17" y1="2" x2="17" y2="32"/>
        <line x1="2" y1="17" x2="32" y2="17"/>
        <line x1="4.5" y1="10" x2="29.5" y2="10"/>
        <line x1="4.5" y1="24" x2="29.5" y2="24"/>
      </svg>
      <span class="contact-text">www.harbor_ledger_funds.com</span>
    </div>

    <div class="contact-row row-address">
      <svg class="contact-icon icon-solid" viewBox="0 0 34 50" aria-hidden="true">
        <path d="M17 2C9 2 3 8 3 16c0 9 14 26 14 26s14-17 14-26C31 8 25 2 17 2zm0 19a5 5 0 1 1 0-10 5 5 0 0 1 0 10z"/>
        <ellipse cx="17" cy="45" rx="11" ry="3.5"/>
      </svg>
      <span class="contact-text">14/C WHARF LANE,<br>14/C WHARF LANE CROSS ROAD</span>
    </div>
  </section>
</div>
</body>
</html>
```